Mindfulness School for Children -- Business Cards

We're looking for business cards for our school directors and owners. We're a mindfulness school for children called little lanterns. Attached are our logos/icons.

```html
<!DOCTYPE html>
<html lang="en">
<head>
<meta charset="utf-8">
<title>little lanterns — Business Cards</title>
<link href="https://fonts.googleapis.com/css2?family=Arimo:wght@400;700&display=swap" rel="stylesheet">
<style>
  :root {
    --backdrop: #1a1a1a;
    --card: #262626;
    --ink: #f2f2f2;
    --teal: #4fb3c6;
    --teal-soft: #6fbfb0;
    --pattern-dark: #141414;
    --pattern-light: #b9b9b9;
  }
  * { margin: 0; padding: 0; box-sizing: border-box; }
  html, body {
    width: 1200px; height: 1059px; overflow: hidden;
    background: var(--backdrop);
    font-family: "Arimo", Arial, sans-serif;
    color: var(--ink);
  }
  .canvas { position: relative; width: 1200px; height: 1059px; }

  .card-front {
    position: absolute; left: 257px; top: 89px;
    width: 687px; height: 390px;
    background: var(--card);
  }
  .brand-name {
    position: absolute; left: 31px; top: 70px;
    font-size: 40px; font-weight: 400; letter-spacing: -0.5px;
    color: var(--teal-soft);
  }
  .holder {
    position: absolute; right: 33px; top: 168px; text-align: right;
  }
  .holder-name {
    font-size: 25px; font-weight: 700; color: var(--teal);
    letter-spacing: 0.2px; line-height: 30px;
  }
  .holder-title { font-size: 16px; line-height: 20px; }
  .accent-bar {
    position: absolute; right: 0; top: 176px;
    width: 15px; height: 40px; background: var(--teal);
  }
  .address {
    position: absolute; left: 31px; top: 221px;
    font-size: 15.5px; line-height: 22px;
  }
  .contacts {
    position: absolute; left: 31px; top: 274px; list-style: none;
    font-size: 15.5px;
  }
  .contacts li {
    display: flex; align-items: center; gap: 7px; height: 26.5px;
  }
  .contacts svg { width: 12px; height: 12px; flex: none; fill: var(--teal); }

  .card-back {
    position: absolute; left: 253px; top: 546px;
    width: 694px; height: 395px;
    background: linear-gradient(100deg, var(--pattern-dark) 0%, #1e1e1e 40%, #5a5a5a 72%, var(--pattern-light) 100%);
  }
</style>
</head>
<body>
<main class="canvas">
  <section class="card-front">
    <div class="brand-name">little lanterns</div>

    <div class="holder">
      <div class="holder-name">DANIEL WHITFORD</div>
      <div class="holder-title">CEO/Founder</div>
    </div>
    <div class="accent-bar"></div>

    <address class="address" style="font-style:normal">
      Po Box 4519 Cedar Lane<br>
      Ridgefield, AB 62390
    </address>

    <ul class="contacts">
      <li>
        <svg viewBox="0 0 24 24" aria-hidden="true"><path d="M6.6 10.8a15 15 0 0 0 6.6 6.6l2.2-2.2c.3-.3.7-.4 1-.2 1.1.4 2.3.6 3.6.6.6 0 1 .4 1 1V20c0 .6-.4 1-1 1A17 17 0 0 1 3 4c0-.6.4-1 1-1h3.5c.6 0 1 .4 1 1 0 1.3.2 2.5.6 3.6.1.3 0 .7-.2 1z"/></svg>
        (00) 5382 1907
      </li>
      <li>
        <svg viewBox="0 0 24 24" aria-hidden="true"><path d="M2 5h20v14H2z M3 6l9 7 9-7" fill="none" stroke="#4fb3c6" stroke-width="2.4"/></svg>
        info@littlelanterns.com
      </li>
      <li>
        <svg viewBox="0 0 24 24" aria-hidden="true"><circle cx="12" cy="12" r="10"/><path d="M7 7c2 0 3 2 2 4s2 3 1 6M15 5c-1 2 1 3 3 3M14 14c2 0 3 2 2 5" fill="none" stroke="#262626" stroke-width="1.6"/></svg>
        www.littlelanterns.com
      </li>
    </ul>
  </section>

  <section class="card-back" role="img" aria-label="Repeating pattern of the brand flower symbol, fading from black on the left to light grey on the right"></section>
</main>
</body>
</html>
```